KHL Flyer Design - Sales Flyer

Using our existing black and red color scheme (logo files attached), we want to create an 8.5 x 16" trifold sales flier template (example attached) for our company. Content/copy is not expected—I only need help with the design/layout. I have shared some images of our operations and people for the flier.
For design themes or other content, you can also look at our website (www.kestrelhaul.com) or the attached PowerPoint presentation.
Target Market(s)
Logistics, trucking, storage
Industry/Entity Type
Logistics, trucking, inventory
Look and feel

```html
<!DOCTYPE html>
<html lang="en">
<head>
<meta charset="utf-8">
<title>KHL Trifold Sales Flyer</title>
<link href="https://fonts.googleapis.com/css2?family=Montserrat:ital,wght@0,400;0,500;0,600;0,700;0,800;1,700&display=swap" rel="stylesheet">
<style>
:root{
  --red:#e21e26;
  --black:#111111;
  --ink:#222222;
  --white:#ffffff;
  --grey-bg:#d5d6d8;
}
*{box-sizing:border-box;margin:0;padding:0}
html,body{width:1200px;height:2945px;overflow:hidden}
body{background:var(--grey-bg);font-family:'Montserrat',sans-serif;color:var(--ink);position:relative}
.spread{position:absolute;left:71px;width:1060px;height:563px;background:var(--white);overflow:hidden;box-shadow:0 6px 14px rgba(0,0,0,.18)}
.spread--outside{top:1500px}
.spread--inside{top:2150px}
.abs{position:absolute}
.photo{position:absolute}
.black{background:var(--black)}
.red{background:var(--red)}
.label{color:var(--white);font-weight:800;text-transform:uppercase}
.body-copy{font-size:7.2px;line-height:1.45;color:var(--white)}
.dark-copy{font-size:7.6px;line-height:1.45;color:var(--ink)}
.brand{font-weight:800;color:var(--red);font-size:40px;letter-spacing:1px}
h3.service{color:var(--red);font-size:12.5px;font-weight:700;margin-bottom:4px}
.stat-num{color:var(--red);font-weight:700;font-size:16px;line-height:1}
.stat-lbl{color:var(--white);font-size:7.4px;margin:2px 0 8px}
.ticks li{list-style:none;font-size:7.6px;font-weight:600;line-height:1.25;padding-left:14px;position:relative;margin-bottom:8px}
.ticks li svg{position:absolute;left:0;top:1px}
.pillar{position:absolute;width:98px;height:98px;border-radius:50%;text-align:center;background:#fff}
.pillar-cap{height:44px;border-radius:49px 49px 0 0;color:#fff;font-size:9px;font-weight:600;padding-top:28px}
.pillar p{font-size:4.6px;line-height:1.45;color:#777;padding:5px 12px 0}
</style>
</head>
<body>

<section class="spread spread--outside">
  <div class="photo" role="img" aria-label="Warehouse with stacks of steel pipe in the yard" style="left:0;top:0;width:176px;height:337px;background:linear-gradient(160deg,#9fb6cf 0%,#d9cdb8 40%,#8a6a52 75%,#5a4a40 100%)"></div>
  <div class="photo" role="img" aria-label="Loader moving pipe across a dusty yard" style="left:176px;top:0;width:177px;height:337px;background:linear-gradient(170deg,#c98f5e 0%,#d9a577 45%,#b07850 100%)"></div>
  <svg class="abs" style="left:100px;top:0" width="253" height="75" viewBox="0 0 253 75"><polygon points="60,0 253,0 253,75" fill="var(--red)"/></svg>
  <div class="abs label" style="left:250px;top:12px;font-size:24px">Story</div>

  <div class="photo" role="img" aria-label="Line drawing of a port, rail, trucks and warehouses" style="left:365px;top:14px;width:470px;height:50px;background:linear-gradient(90deg,#f4f4f4,#ececec,#f4f4f4)"></div>
  <div class="photo" role="img" aria-label="Worker in hard hat inspecting pipe" style="left:353px;top:74px;width:176px;height:263px;background:linear-gradient(160deg,#e9e6df 0%,#f08a3a 45%,#3b4a5a 80%,#6a5d54 100%)"></div>
  <div class="photo" role="img" aria-label="Rows of pipe laid out on racks" style="left:529px;top:74px;width:177px;height:263px;background:linear-gradient(170deg,#d8c9b0 0%,#9c8a6c 45%,#5c6e63 80%,#7a6f5c 100%)"></div>

  <div class="abs" style="left:870px;top:18px;width:165px;text-align:right"><span class="brand">KHL</span></div>
  <div class="photo" role="img" aria-label="Red semi-truck with trailer in a loading yard" style="left:706px;top:74px;width:354px;height:320px;background:linear-gradient(170deg,#b9bec4 0%,#8d939a 35%,#a2232a 58%,#2b2b2b 85%,#111 100%)"></div>
  <div class="abs" style="left:732px;top:92px;font-size:26px;line-height:.95;font-weight:800;color:transparent;-webkit-text-stroke:1.4px var(--red)">EXCELLENCE<br>IN ACTION.</div>

  <div class="abs black" style="left:0;top:337px;width:706px;height:208px"></div>
  <div class="abs black" style="left:706px;top:394px;width:354px;height:136px"></div>

  <div class="abs label" style="left:21px;top:355px;font-size:14px;line-height:1.05;width:300px">Setting the standard<br>in logistics with precision<br>and transparency</div>
  <svg class="abs" style="left:262px;top:369px" width="30" height="18" viewBox="0 0 30 18"><rect x="0" y="3" width="18" height="11" fill="var(--red)"/><rect x="18" y="7" width="10" height="7" fill="var(--red)"/><circle cx="6" cy="16" r="2" fill="#fff"/><circle cx="23" cy="16" r="2" fill="#fff"/></svg>
  <div class="abs body-copy" style="left:21px;top:412px;width:205px;font-size:6.7px;line-height:1.42">No one brings more precision and expertise to supply chain and inventory management than KHL. Since 2011, we have demonstrated an ability to keep it simple – getting your product to the right place at the right time. We have highly skilled personnel utilizing cutting-edge equipment and processes to load/unload, store, and transport your product safely and efficiently – no matter the location.<br><br>Our unique ERP software provides seamless planning and real-time tracking of your products – from source to final destination – with full transparency at every step.</div>
  <div class="abs" style="left:238px;top:405px">
    <div class="stat-num">20000</div><div class="stat-lbl">Monthly Tonnage Volume</div>
    <div class="stat-num">525</div><div class="stat-lbl">Monthly Truckloads</div>
    <div class="stat-num">30000</div><div class="stat-lbl">Average Tons in Storage</div>
    <div class="stat-num">40</div><div class="stat-lbl">Monthly Railcars</div>
  </div>

  <div class="abs label" style="left:353px;top:356px;width:353px;text-align:center;font-size:14px">Let's work together</div>
  <div class="abs body-copy" style="left:378px;top:378px;width:303px;text-align:center;font-size:7.8px">We understand that every business is unique. Our team will work closely with you to create custom solutions that meet your specific needs and challenges. Partner with us for seamless, reliable, and cost-effective logistics solutions tailored to your business needs.</div>
  <div class="abs" style="left:410px;top:436px;width:240px;height:1px;background:var(--red)"></div>
  <div class="abs" style="left:353px;top:447px;width:353px;text-align:center;color:#fff;font-size:11.5px;font-weight:500;line-height:1.55">www.kestrelhaul.com<br>contact@kestrelhaul.com</div>
  <svg class="abs" style="left:375px;top:500px" width="310" height="45" viewBox="0 0 310 45"><polygon points="18,0 310,0 300,45 0,45" fill="var(--red)"/></svg>
  <svg class="abs" style="left:423px;top:510px" width="24" height="24" viewBox="0 0 24 24"><circle cx="12" cy="12" r="11" fill="#fff"/><path d="M8 6l2.5 0 1 3-1.5 1.2a8 8 0 0 0 3.8 3.8L15 12.5l3 1V16a2 2 0 0 1-2 2A10 10 0 0 1 6 8a2 2 0 0 1 2-2z" fill="var(--black)"/></svg>
  <div class="abs" style="left:453px;top:506px;color:#fff;font-size:22px;font-weight:600">(555) 014-2290</div>

  <div class="abs red label" style="left:740px;top:405px;padding:3px 9px;font-size:8.5px;font-weight:700">Logistics Redefined</div>
  <div class="abs" style="left:732px;top:422px;color:#fff;font-size:21px;line-height:1.05;font-weight:400">Tailored Solutions for<br>Your Business Needs</div>
  <div class="abs body-copy" style="left:732px;top:476px;width:260px;font-size:7.8px">We are a leading provider of innovative and dependable logistics solutions, known for our steadfast commitment to safety, reliability, and exceptional customer service.</div>
  <div class="abs" style="left:860px;top:541px;width:180px;text-align:right;font-size:8.5px;font-weight:700;color:var(--black)">KESTRELHAUL<span style="color:var(--red)">.COM</span></div>
</section>

<section class="spread spread--inside">
  <div class="abs black" style="left:0;top:0;width:706px;height:73px"></div>
  <svg class="abs" style="left:700px;top:0" width="360" height="73" viewBox="0 0 360 73"><rect width="360" height="73" fill="var(--red)"/></svg>
  <div class="abs" style="left:720px;top:10px"><span class="brand" style="color:#fff;font-size:34px">KHL</span></div>

  <svg class="abs" style="left:55px;top:29px" width="180" height="27" viewBox="0 0 180 27"><polygon points="6,0 180,0 174,27 0,27" fill="var(--red)"/></svg>
  <div class="abs label" style="left:83px;top:34px;font-size:16px">View our services</div>
  <svg class="abs" style="left:403px;top:29px" width="185" height="27" viewBox="0 0 185 27"><polygon points="6,0 185,0 179,27 0,27" fill="var(--red)"/></svg>
  <div class="abs label" style="left:429px;top:34px;font-size:16px">Why work with KHL?</div>

  <div class="photo" role="img" aria-label="Orange wheel loader with forks on a flatbed trailer" style="left:0;top:73px;width:353px;height:280px;background:linear-gradient(170deg,#8fb5de 0%,#c8d8e6 35%,#b49a78 60%,#e19044 75%,#6a5a4c 100%)"></div>
  <svg class="abs" style="left:0;top:240px" width="353" height="120" viewBox="0 0 353 120"><polygon points="0,120 353,0 353,120" fill="#fff"/></svg>
  <svg class="abs" style="left:122px;top:322px" width="42" height="24" viewBox="0 0 42 24"><rect x="0" y="4" width="26" height="14" fill="var(--red)"/><rect x="26" y="9" width="14" height="9" fill="var(--red)"/><circle cx="8" cy="21" r="3" fill="#333"/><circle cx="32" cy="21" r="3" fill="#333"/></svg>
  <div class="abs" style="left:20px;top:350px;width:145px">
    <h3 class="service">Transloading</h3>
    <p class="dark-copy">Our comprehensive logistics services cover every aspect of rail transportation, from the point of origin to the final destination. We assess the required manpower and utilize the right equipment designed to handle the project from start to finish.</p>
    <h3 class="service" style="margin-top:14px">Forklift/Crane Rentals</h3>
    <p class="dark-copy">We provide forklift and crane rentals to facilitate quick loading/unloading and stringing of pipe. We transport the right equipment with qualified machine operators and spotters (if required) to your location.</p>
  </div>
  <div class="abs" style="left:190px;top:310px;width:150px">
    <h3 class="service">Transportation</h3>
    <p class="dark-copy">From forklifts to trucking, transloading to inspection, we have top-quality options that support you at each step of the process. Our team is expertly trained to efficiently move your supplies and products.</p>
    <h3 class="service" style="margin-top:12px">Storage</h3>
    <p class="dark-copy">Our customized storage solutions let you expand your market reach and forward-position inventory for lower freight costs and efficient distribution.</p>
    <h3 class="service" style="margin-top:12px">Inspection</h3>
    <p class="dark-copy">Trust us to ensure the reliability and safety of your OCTG material. We ensure your product is free from defects by performing both visual and non-destructive testing (NDT).</p>
  </div>

  <div class="photo" role="img" aria-label="White semi-truck hauling an oversize load" style="left:353px;top:73px;width:176px;height:180px;background:linear-gradient(170deg,#a9c2db 0%,#d9dde0 45%,#9a9a92 75%,#c7a36a 100%)"></div>
  <div class="photo" role="img" aria-label="Two workers in hard hats reviewing paperwork on site" style="left:529px;top:73px;width:177px;height:180px;background:linear-gradient(160deg,#5a4a3e 0%,#2b3446 45%,#e6e6e6 70%,#7a6a58 100%)"></div>
  <div class="abs dark-copy" style="left:370px;top:263px;width:320px;text-align:center">Choosing the right logistics partner makes all the difference, and Kestrel Haul &amp; Logistics (KHL) is dedicated to providing exceptional service, reliability, and transparency at every stage of the supply chain. Our team understands the unique demands of logistics, and we leverage our expertise to create seamless, efficient solutions tailored to our clients' needs.</div>
  <ul class="ticks abs" style="left:399px;top:323px;width:140px">
    <li><svg width="9" height="9" viewBox="0 0 9 9"><circle cx="4.5" cy="4.5" r="4" fill="none" stroke="var(--red)"/><path d="M2.5 4.6l1.5 1.4 2.6-2.8" stroke="var(--red)" fill="none"/></svg>SAFE, TIMELY, ACCURATE, and RELIABLE</li>
    <li><svg width="9" height="9" viewBox="0 0 9 9"><circle cx="4.5" cy="4.5" r="4" fill="none" stroke="var(--red)"/><path d="M2.5 4.6l1.5 1.4 2.6-2.8" stroke="var(--red)" fill="none"/></svg>Always in the know about where your inventory is and when it is delivered</li>
  </ul>
  <ul class="ticks abs" style="left:543px;top:323px;width:150px">
    <li><svg width="9" height="9" viewBox="0 0 9 9"><circle cx="4.5" cy="4.5" r="4" fill="none" stroke="var(--red)"/><path d="M2.5 4.6l1.5 1.4 2.6-2.8" stroke="var(--red)" fill="none"/></svg>Proprietary planning and management systems</li>
    <li><svg width="9" height="9" viewBox="0 0 9 9"><circle cx="4.5" cy="4.5" r="4" fill="none" stroke="var(--red)"/><path d="M2.5 4.6l1.5 1.4 2.6-2.8" stroke="var(--red)" fill="none"/></svg>Real-time reporting of your inventory and deliveries</li>
  </ul>
  <svg class="abs" style="left:670px;top:375px" width="14" height="40" viewBox="0 0 14 40"><polygon points="9,0 14,0 5,40 0,40" fill="var(--red)"/></svg>
  <div class="abs" style="left:353px;top:405px;width:353px;text-align:center;color:var(--red);font-size:19px;font-weight:400;letter-spacing:.5px">VISION &amp; PURPOSE</div>
  <div class="pillar" style="left:373px;top:437px;box-shadow:0 1px 4px rgba(0,0,0,.2)">
    <div class="pillar-cap red">VISION</div>
    <p>To be the leading provider of innovative and reliable logistics solutions, recognized for unwavering dedication to safety, reliability, and superior customer service.</p>
  </div>
  <div class="pillar" style="left:480px;top:437px;box-shadow:0 1px 4px rgba(0,0,0,.2)">
    <div class="pillar-cap black">INNOVATION</div>
    <p>We leverage cutting-edge technologies to streamline supply chains and maximize value while keeping it simple – getting your product to the right place at the right time.</p>
  </div>
  <div class="pillar" style="left:587px;top:437px;box-shadow:0 1px 4px rgba(0,0,0,.2)">
    <div class="pillar-cap black">PEOPLE</div>
    <p>We are passionate about every job we undertake. You can count on our team to complete each task with integrity, dedication, and enthusiasm.</p>
  </div>
  <svg class="abs" style="left:414px;top:443px" width="16" height="16" viewBox="0 0 20 20"><circle cx="10" cy="10" r="8" fill="none" stroke="#fff" stroke-width="1.4"/><circle cx="10" cy="10" r="2.5" fill="#fff"/></svg>
  <svg class="abs" style="left:521px;top:443px" width="16" height="16" viewBox="0 0 20 20"><circle cx="10" cy="10" r="8" fill="none" stroke="#fff" stroke-width="1.4"/><circle cx="10" cy="9" r="3" fill="#fff"/><rect x="8.5" y="12" width="3" height="3" fill="#fff"/></svg>
  <svg class="abs" style="left:628px;top:443px" width="16" height="16" viewBox="0 0 20 20"><circle cx="10" cy="10" r="8" fill="none" stroke="#fff" stroke-width="1.4"/><circle cx="10" cy="7.5" r="2" fill="#fff"/><rect x="7" y="10.5" width="6" height="4" rx="1.5" fill="#fff"/></svg>

  <div class="photo" role="img" aria-label="Worker inspecting stacked pipe ends" style="left:706px;top:73px;width:176px;height:185px;background:linear-gradient(170deg,#8ba8c6 0%,#b7b1a6 40%,#6d7a88 70%,#504a44 100%)"></div>
  <div class="photo" role="img" aria-label="Long rows of pipe stretching across an oilfield yard" style="left:882px;top:0;width:178px;height:258px;background:linear-gradient(175deg,#7da3cc 0%,#b7c7d8 30%,#c49a6a 55%,#8a5c36 100%)"></div>
  <svg class="abs" style="left:720px;top:258px" width="200" height="130" viewBox="0 0 200 130"><polygon points="25,0 200,0 175,130 0,130" fill="var(--red)"/></svg>
  <div class="photo" role="img" aria-label="Smiling worker in hard hat and coveralls" style="left:765px;top:258px;width:150px;height:130px;background:linear-gradient(170deg,#e0a238 0%,#8a5e40 35%,#2e4f8a 70%,#203a66 100%)"></div>
  <div class="abs" style="left:915px;top:264px;width:145px;font-size:15px;line-height:1.12;color:var(--black)">Empowering<br>Progress as a<br><b style="font-weight:800">Proud<br>Minority-Owned<br>Business</b></div>
  <div class="abs dark-copy" style="left:730px;top:400px;width:310px;text-align:center">At KHL, we are proud to be a minority-owned company, bringing unique perspectives and a commitment to inclusivity in the logistics industry. Our leadership and team are dedicated to delivering top-quality logistics solutions in every aspect of our business.<br><br>As a member of the NSBA (National Supplier Bridge Alliance) and a recognized MBE (Minority-Owned Business Enterprise) by the Supplier Registry Network, we can help your company (or your customers such as public utilities, governmental agencies or healthcare companies) meet spend requirements, government regulations, contractual obligations, and corporate social responsibility targets.<br><br>Partnering with KHL means working with a company that champions diversity, values every voice, and strives to make a meaningful impact every day.</div>
</section>

</body>
</html>
```